Help our Sugar Loom find our winning design! We're looking for a business card....

We’re a Sugar Loom in NY specializing in custom-made cakes and unique desserts.
Our cakes combine flavor and art, each designed to match customer’s special event and theme.
We’d like a unique business card with a clean design that will combine French chic and artistic look & feel.
We’d like to differentiate ourselves from standard bakeries, please don’t offer cupcake images :-)
Our logo is peach-pink and brown and we’d love to use these colors ( . Another color that can be added is gold - or feel free to suggest!

Target Market(s)

Women, ages 25-55

Industry/Entity Type

Boutique

Contact Information for Business Card

Text on card:
Logo
Sugar Loom by Dana Welch

www.sugarloomsweets.com
hello@sugarloom.com
(516) 555-0147
F – sugarloomnyc
IG - sugarloom_ny

Font styles to use
Sans Serif
Script

Requirements
Must have
• Logo
• Clean look
• French chic and artistic look & feel.
Nice to have
• Damask pattern
Should not have
• Cupcake images

```html
<!DOCTYPE html>
<html lang="en">
<head>
<meta charset="utf-8">
<title>Sugar Loom – Business Card</title>
<link href="https://fonts.googleapis.com/css2?family=Montserrat:wght@400;600&display=swap" rel="stylesheet">
<style>
  :root {
    --page: #e9e7e5;
    --card: #ffffff;
    --cocoa: #67625f;
    --ink: #3f3b39;
    --blush: #ef8fa4;
    --white: #ffffff;
  }
  * { margin: 0; padding: 0; box-sizing: border-box; }
  html, body {
    width: 1200px; height: 901px; overflow: hidden;
    background: var(--page);
    font-family: "Montserrat", sans-serif;
  }
  .sheet {
    width: 1200px; height: 901px;
    display: flex; flex-direction: column; align-items: center; justify-content: center;
    gap: 40px;
  }
  .card {
    position: relative;
    width: 680px; height: 388px;
    background: var(--card);
    border-radius: 34px;
    overflow: hidden;
    box-shadow: 0 6px 18px rgba(0,0,0,0.12);
  }
  .brand-name {
    color: var(--blush);
    font-weight: 400;
    letter-spacing: 0.04em;
    white-space: nowrap;
  }
  /* Front */
  .card--front { display: flex; align-items: center; justify-content: center; }
  .card--front .brand-name { font-size: 56px; }

  /* Back */
  .back-shape { position: absolute; inset: 0; width: 100%; height: 100%; }
  .holder { position: absolute; left: 44px; top: 40px; }
  .holder-name {
    font-weight: 600; font-size: 26px; letter-spacing: 0.06em;
    color: var(--ink); text-transform: uppercase;
  }
  .holder-role { margin-top: 6px; font-size: 14px; color: var(--ink); }
  .card--back .brand-name {
    position: absolute; right: 60px; top: 50px; font-size: 32px;
  }
  .contacts {
    position: absolute; right: 44px; bottom: 30px;
    list-style: none; color: var(--white);
    font-size: 14px; line-height: 22px; text-align: right;
  }
  .contacts li { display: flex; align-items: center; justify-content: flex-end; gap: 10px; }
  .contacts .icon { width: 13px; height: 13px; flex: none; fill: var(--white); }
  .contacts .icon-space { width: 13px; flex: none; }
  .contacts .gap { margin-top: 8px; }
</style>
</head>
<body>
<main class="sheet">
  <section class="card card--front" aria-label="Card front">
    <span class="brand-name">Sugar Loom</span>
  </section>

  <section class="card card--back" aria-label="Card back">
    <svg class="back-shape" viewBox="0 0 680 388" preserveAspectRatio="none" aria-hidden="true">
      <path d="M0 138 C 220 156, 440 214, 680 168 L680 388 L0 388 Z" fill="var(--blush)"/>
      <path d="M0 150 C 220 170, 440 232, 680 186 L680 388 L0 388 Z" fill="var(--cocoa)"/>
    </svg>

    <div class="holder">
      <p class="holder-name">Dana Welch</p>
      <p class="holder-role">Managing Director</p>
    </div>
    <span class="brand-name">Sugar Loom</span>

    <ul class="contacts">
      <li>214 Mercer Street<span class="icon-space"></span></li>
      <li>New York NY
        <svg class="icon" viewBox="0 0 12 12"><path d="M6 0a4 4 0 0 0-4 4c0 3 4 8 4 8s4-5 4-8a4 4 0 0 0-4-4zm0 5.5A1.5 1.5 0 1 1 6 2.5a1.5 1.5 0 0 1 0 3z"/></svg>
      </li>
      <li>(516) 555-0147
        <svg class="icon" viewBox="0 0 12 12"><path d="M2.5 0.5l2 2-1 1.5a7 7 0 0 0 4.5 4.5l1.5-1 2 2-1.5 2C5 11 1 7 0.5 2z"/></svg>
      </li>
      <li class="gap">hello@sugarloom.com
        <svg class="icon" viewBox="0 0 12 12"><path d="M0 2h12v8H0z M0.8 2.6L6 6.6l5.2-4" fill="none" stroke="#fff" stroke-width="1.2"/></svg>
      </li>
      <li>www.sugarloomsweets.com
        <svg class="icon" viewBox="0 0 12 12"><circle cx="6" cy="6" r="5.2" fill="none" stroke="#fff" stroke-width="1.2"/><path d="M0.8 6h10.4M6 0.8c-3 3-3 7.4 0 10.4M6 0.8c3 3 3 7.4 0 10.4" fill="none" stroke="#fff" stroke-width="1"/></svg>
      </li>
    </ul>
  </section>
</main>
</body>
</html>
```